The K7 Momentum Collective Website

We have a pitch deck and messaging drafted. Target audience is academic institutions and VC investors that have seed money in start ups.

Need a basic website

Industry/Entity Type

LIfe Science, Diagnostic, medical device.

Coding

Coded - Design and coding required

Number of Pages Required

5+ page

```html
<!DOCTYPE html>
<html lang="en">
<head>
<meta charset="utf-8">
<title>The K7 Momentum Collective</title>
<link href="https://fonts.googleapis.com/css2?family=Poppins:wght@300;400;500;600&display=swap" rel="stylesheet">
<style>
:root{
  --navy:#081a30;
  --navy-2:#0d2a4a;
  --blue:#0a6fc2;
  --blue-bright:#1e8cf0;
  --ink:#1b1b1b;
  --body:#333;
  --map:#c9cbcf;
  --line:#d0d3d8;
  --bar:#2c3847;
  --white:#fff;
}
*{box-sizing:border-box;margin:0;padding:0}
html,body{width:1200px;height:3731px;overflow:hidden}
body{position:relative;font-family:'Poppins',sans-serif;color:var(--body);background:var(--white)}
.abs{position:absolute}
a{color:inherit;text-decoration:none}
.btn{position:absolute;background:var(--blue);color:#fff;font-size:14px;display:flex;align-items:center;justify-content:center}

/* hero */
.hero{left:0;top:0;width:1200px;height:560px;background:radial-gradient(ellipse at 70% 40%,var(--navy-2),var(--navy) 70%)}
.brand{display:flex;align-items:center;gap:8px;font-weight:500;color:var(--blue-bright);font-size:13px;letter-spacing:.5px}
.brand .dot{width:12px;height:12px;border-radius:50%;background:var(--blue-bright)}
.nav{left:381px;top:50px;display:flex;gap:37px;color:#fff;font-size:14px}
.signin{left:898px;top:48px;color:#fff;font-size:14px}
.signup{left:972px;top:44px;width:108px;height:30px;background:#8a8f96;color:#fff;font-size:14px;display:flex;align-items:center;justify-content:center}
.hero h1{left:120px;top:196px;color:#fff;font-weight:300;font-size:47px;line-height:57px}
.hero-visual{left:577px;top:232px;width:575px;height:378px;border-radius:18px 18px 6px 6px;background:linear-gradient(160deg,#b9d3ea,#6f9fcf 55%,#c4c8cd 85%)}
.scroll-mouse{left:589px;top:626px}

/* section heads */
.eyebrow{width:1200px;left:0;text-align:center;font-size:16px;color:var(--ink)}
.title{width:1200px;left:0;text-align:center;font-size:35px;font-weight:400;color:var(--ink)}
.about-text{left:200px;top:835px;width:800px;text-align:center;font-size:15.5px;line-height:24px;color:#333;font-weight:300}

/* team */
.team-bg{left:0;top:1111px;width:1200px;height:1063px;background:linear-gradient(160deg,#e6e8eb,#f3f4f6 60%,#e9ebee)}
.grid{left:83px;top:1285px;width:1028px;height:761px;display:grid;grid-template-columns:339px 345px 344px;grid-template-rows:381px 380px;box-shadow:0 2px 14px rgba(0,0,0,.08);background:#fff}
.photo{position:relative}
.photo .ph{position:absolute;inset:0}
.contact-tag{position:absolute;bottom:0;left:130px;right:0;background:rgba(255,255,255,.72);padding:8px 0 10px 48px;font-size:16px;line-height:28px;color:#111}
.bio{position:relative;text-align:center;padding:38px 22px 0}
.bio h3{font-weight:400;font-size:32px;color:var(--ink);margin-bottom:18px}
.bio p{font-size:15px;line-height:27.4px;color:#333;font-weight:300;height:219px;overflow:hidden}
.bio .more{display:inline-block;font-size:15px;text-decoration:underline;margin-top:2px;color:#222}
.pill{position:absolute;background:var(--blue);border-radius:20px}

/* plan */
.card{top:2401px;width:223px;height:325px;background:var(--blue);border-radius:12px;color:#fff;text-align:center;padding:80px 10px 0}
.card h4{font-weight:500;font-size:17.5px;margin-bottom:10px}
.card p{font-size:13.5px;line-height:22.5px;font-weight:300}
.badge{top:2343px;width:122px;height:122px;border-radius:50%;background:#fff;box-shadow:0 2px 6px rgba(0,0,0,.12);display:flex;align-items:center;justify-content:center}

/* contact */
.map{left:0;top:2780px;width:1200px;height:498px}
.addr-card{left:897px;top:2927px;width:217px;height:73px;background:#fff;font-size:13.5px;line-height:24px;padding:12px 10px 0 42px;color:#222}
.form-card{left:114px;top:2988px;width:502px;height:424px;background:#fff}
.field{position:absolute;left:42px;width:409px;height:59px;border:1px solid var(--line);font-size:14px;color:#888;padding:18px 28px}

/* footer */
.f-col h5{font-size:12px;font-weight:600;color:#111;margin-bottom:12px}
.f-col li{list-style:none;font-size:12.5px;line-height:22px;color:#222}
.bar{left:0;top:3670px;width:1200px;height:61px;background:var(--bar);color:#fff;font-size:11px;display:flex;align-items:center;justify-content:center}
</style>
</head>
<body>

<!-- Hero -->
<section class="abs hero">
  <div class="abs brand" style="left:120px;top:48px"><span class="dot"></span>THE K7 MOMENTUM COLLECTIVE</div>
  <nav class="abs nav"><a>Home</a><a>About Us</a><a>Our Team</a><a>Our Plan</a><a>Contact</a></nav>
  <a class="abs signin">Sign In</a>
  <a class="abs signup">Sign Up</a>
  <h1 class="abs">Accelerating Your<br>Innovative IP<br>To Market!</h1>
  <a class="btn" style="left:123px;top:393px;width:106px;height:30px;font-size:13px">Get Started</a>
</section>
<div class="abs hero-visual" role="img" aria-label="Laptop showing a person viewing market data dashboards"></div>
<svg class="abs scroll-mouse" width="24" height="50" viewBox="0 0 24 50" aria-hidden="true">
  <rect x="2" y="1" width="20" height="30" rx="10" fill="none" stroke="#222" stroke-width="1.6"/>
  <line x1="12" y1="8" x2="12" y2="13" stroke="#222" stroke-width="1.6"/>
  <path d="M12 34v13M7 42l5 5 5-5" fill="none" stroke="#222" stroke-width="1.6"/>
</svg>

<!-- About -->
<div class="abs eyebrow" style="top:735px">ABOUT US</div>
<h2 class="abs title" style="top:763px">The K7 Momentum Collective™</h2>
<p class="abs about-text">The K7 Momentum Collective (K7) is a group of experienced executives whose careers have been focused on taking innovative ideas to market by strategically navigating the buildout of best-in-class life science and diagnostic organizations. This experience makes us uniquely equipped to be involved in all aspects of your due diligence on new or existing investments (business analysis, industry thesis, competitive landscape, business/pricing model, and financial modeling as it relates to validation of the assumptions in the model to determine the return expectations).</p>
<a class="btn" style="left:546px;top:1007px;width:107px;height:30px">Read More</a>

<!-- Team -->
<div class="abs team-bg"></div>
<div class="abs eyebrow" style="top:1167px">TEAM</div>
<h2 class="abs title" style="top:1195px">Meet The Partners</h2>
<div class="abs grid">
  <div class="photo"><div class="ph" role="img" aria-label="Portrait of partner RM Carver" style="background:linear-gradient(135deg,#8a8076,#c9b7a4 50%,#5c5650)"></div>
    <div class="contact-tag">(555) 201-4417<br>rm@k7mc.com</div></div>
  <div class="bio"><h3>RM Carver</h3>
    <p>RM is an accomplished CEO and well-rounded executive with more than 25 years of experience in medical devices, research tools and diagnostics. He has extensive experience in strategy development &amp; deployment, corporate development, private &amp; public capital raise, building</p>
    <a class="more">Read More</a></div>
  <div class="photo"><div class="ph" role="img" aria-label="Portrait of partner LK Marsh" style="background:linear-gradient(135deg,#e9e6e0,#d9b8a0 55%,#8d7c6e)"></div>
    <div class="contact-tag" style="left:0;padding-left:48px">(555) 318-7720<br>lk@k7mc.com</div></div>
  <div class="bio"><h3>Dana Whitlock</h3>
    <p>Dana has over 30 years of experience in the quality, regulatory and operations field in medical devices, companion diagnostics, education, and health care systems. She has extensive executive experience in establishing the quality and regulatory path forward for numerus</p>
    <a class="more">Read More</a></div>
  <div class="photo"><div class="ph" role="img" aria-label="Portrait of partner Dana Whitlock" style="background:linear-gradient(135deg,#d9c4a6,#e8d7bf 50%,#9a8468)"></div>
    <div class="contact-tag" style="left:140px;padding-left:45px">(555)402-9135<br>dana@k7mc.com</div></div>
  <div class="bio" style="padding-top:48px"><h3>LK Marsh</h3>
    <p style="height:218px">LK is a proven marketing, sales and operations executive leader in the life science and diagnostic industries. She has extensive experience in assessing and developing business plans and growth strategies that include business analysis, industry thesis, competitive landscape</p>
    <a class="more">Read More</a></div>
</div>
<div class="abs pill" style="left:375px;top:1331px;width:100px;height:40px"></div>
<div class="abs pill" style="left:1039px;top:1615px;width:42px;height:100px"></div>
<div class="abs pill" style="left:381px;top:1986px;width:100px;height:40px"></div>

<!-- Plan -->
<div class="abs eyebrow" style="top:2227px">OUR PLAN</div>
<h2 class="abs title" style="top:2255px">K7 Plan Elements</h2>

<div class="abs card" style="left:120px"><h4>Executive Summary</h4><p>Articulates a brief snapshot of the business model/plan, including name, location, products or services, mission statement, and organizational values/ cultural beliefs.</p></div>
<div class="abs card" style="left:365px"><h4>Company Description</h4><p>Describes a high-level view of the business nature, customer need being met, history, legality, short term, and long-term goals.</p></div>
<div class="abs card" style="left:611px"><h4>Products/Services</h4><p>Provides a description of the product/services, its competitive advantages, customer benefits, reimbursement, estimated supplier costs, the net revenue from the sale of the product or service and after sale support.</p></div>
<div class="abs card" style="left:857px"><h4>Market Analysis</h4><p>Displays research and plan to reach the target demographic as well as the size, direction, and competitors in the overall industry.</p></div>

<div class="abs badge" style="left:170px"><svg width="54" height="54" viewBox="0 0 54 54" fill="none" stroke="#222" stroke-width="2"><rect x="8" y="6" width="30" height="42"/><path d="M14 16h18M14 24h18M14 32h12M44 14L30 38l-4 6 6-4 16-24z"/></svg></div>
<div class="abs badge" style="left:416px"><svg width="54" height="54" viewBox="0 0 54 54" fill="none" stroke="#222" stroke-width="2"><rect x="8" y="8" width="30" height="40"/><rect x="16" y="4" width="14" height="7"/><path d="M14 20h6M14 28h6M14 36h6M24 20h8M24 28h8"/><circle cx="40" cy="38" r="7"/></svg></div>
<div class="abs badge" style="left:662px"><svg width="54" height="54" viewBox="0 0 54 54" fill="none" stroke="#222" stroke-width="2"><path d="M8 26l16-8 16 8-16 8zM8 26v14l16 8 16-8V26M24 34v14"/><circle cx="26" cy="8" r="5"/><circle cx="42" cy="42" r="6"/></svg></div>
<div class="abs badge" style="left:908px"><svg width="54" height="54" viewBox="0 0 54 54" fill="none" stroke="#222" stroke-width="2"><path d="M6 48h42M12 48V30h6v18M22 48V22h6v26M32 48V34h6v14M42 48V26"/><circle cx="40" cy="10" r="6"/><path d="M8 26l10-8 8 6 10-10"/></svg></div>

<a class="btn" style="left:546px;top:2770px;width:107px;height:30px">View More</a>

<!-- Contact -->
<div class="abs map" role="img" aria-label="Street map around the office location" style="background:var(--map);clip-path:polygon(0 77px,1030px 77px,1200px 0,1200px 498px,0 498px)"></div>
<div class="abs addr-card">
  <svg class="abs" style="left:16px;top:14px" width="14" height="18" viewBox="0 0 14 18"><path d="M7 1a6 6 0 0 0-6 6c0 4 6 10 6 10s6-6 6-10a6 6 0 0 0-6-6z" fill="#e0303a"/><circle cx="7" cy="7" r="2.2" fill="#fff"/></svg>
  #1, Sample Street, Sample City - 8588
</div>
<svg class="abs" style="left:824px;top:2993px" width="14" height="18" viewBox="0 0 14 18"><path d="M7 1a6 6 0 0 0-6 6c0 4 6 10 6 10s6-6 6-10a6 6 0 0 0-6-6z" fill="#e0303a"/><circle cx="7" cy="7" r="2.2" fill="#fff"/></svg>

<div class="abs form-card">
  <div class="abs" style="left:42px;top:32px;font-size:16px;color:#222">GET IN TOUCH</div>
  <div class="abs" style="left:42px;top:58px;font-size:27px;color:#111">Contact</div>
  <div class="field" style="top:113px">Name</div>
  <div class="field" style="top:194px">Email Address</div>
  <div class="field" style="top:272px">Phone</div>
  <a class="btn" style="left:198px;top:366px;width:107px;height:31px">Submit</a>
</div>
<svg class="abs" style="left:1124px;top:3320px" width="26" height="56" viewBox="0 0 26 56" aria-hidden="true" fill="none" stroke="#222" stroke-width="1.6">
  <path d="M13 16V2M8 7l5-5 5 5"/><rect x="3" y="22" width="20" height="31" rx="10"/><line x1="13" y1="33" x2="13" y2="38"/>
</svg>

<!-- Footer -->
<div class="abs brand" style="left:120px;top:3495px;font-size:14px"><span class="dot"></span>THE K7 MOMENTUM COLLECTIVE</div>
<p class="abs" style="left:120px;top:3562px;width:280px;font-size:12.5px;line-height:19px;color:#222">The K7 Momentum Collective (K7) rapidly brings innovative and transformational IP to market by assisting with all elements of a company's development.</p>
<div class="abs f-col" style="left:510px;top:3463px"><h5>IMPORTANT LINKS</h5><ul><li>Home</li><li>About Us</li><li>Our Team</li><li>Our Plan</li><li>Contact</li></ul></div>
<div class="abs f-col" style="left:737px;top:3463px"><h5>ADDRESS</h5><ul><li>#1, Sample City</li><li>Sample City,</li><li>USA - 57486.</li></ul></div>
<div class="abs f-col" style="left:943px;top:3463px"><h5>COMPANY</h5><ul><li>Contact</li><li>Private Details</li><li>Privacy Policy</li><li>Terms And Condition</li></ul></div>
<div class="abs bar">© Copyrights The K7 Momentum Collective | All Rights Reserved</div>

</body>
</html>
```